Envelope Design - Winner can do follow-up business

- Varnoko.com is a Swiss-based online store selling business shirts and accessories for business men
- Please visit the webpage to make yourself familiar with the company. Although the text is in German, with Plimbo translator you should be able to understand the main content.
- Our clients are mainly business men between 30 and 60 years old. Mostly with a high income working in the service industry (banking, insurance, lawyers, etc.). Sometimes there wives purchase the shirts for them ;-)
- The colors and the logo are given, as they are also used for the print materials (please see files in attachment)
- I am running several businesses and often need a talented web designer --> the winner gets substantial follow-up business
your task:
-for our company we need a new envelope design
-It should be simple and modern
-please use one of the logos in the followings.
-suprise me :)

```html
<!DOCTYPE html>
<html lang="en">
<head>
<meta charset="utf-8">
<title>Varnoko Envelope Set</title>
<link href="https://fonts.googleapis.com/css2?family=Josefin+Sans:wght@600&family=Roboto+Slab:wght@400&display=swap" rel="stylesheet">
<style>
  :root {
    --backdrop: #e9e6e1;
    --paper: #ffffff;
    --paper-shade: #f4f4f6;
    --brand-red: #ee2e24;
    --brand-black: #000000;
    --brand-gold: #e3d35a;
    --gold-faint: #fbf9ea;
    --ink: #333333;
    --mark-on-red: #f7735c;
    --mark-on-black: #a39a80;
  }
  * { margin: 0; padding: 0; box-sizing: border-box; }
  html, body { width: 1200px; height: 980px; overflow: hidden; }
  body { background: var(--backdrop); position: relative; }

  .envelope {
    position: absolute;
    width: 1015px;
    height: 453px;
    background: var(--paper);
    box-shadow: 0 4px 14px rgba(0,0,0,0.18);
    overflow: hidden;
  }
  .envelope--back-red { left: 142px; top: 60px; }
  .envelope--back-black { left: 110px; top: 259px; background: linear-gradient(120deg, var(--paper-shade), var(--paper)); }
  .envelope--front { left: 41px; top: 479px; }

  .flap { position: absolute; left: 0; top: 0; width: 1015px; height: 190px; }
  .flap-name {
    position: absolute;
    left: 0; width: 100%;
    top: 62px;
    text-align: center;
    font-family: "Josefin Sans", sans-serif;
    font-weight: 600;
    font-size: 26px;
    letter-spacing: 3px;
  }
  .envelope--back-red .flap-name { color: var(--mark-on-red); }
  .envelope--back-black .flap-name { color: var(--mark-on-black); }

  .front-band { position: absolute; left: 0; top: 0; width: 100%; height: 46px; background: var(--brand-black); }
  .front-rule { position: absolute; left: 0; top: 48px; width: 100%; height: 2px; background: var(--brand-red); }
  .front-base { position: absolute; left: 0; bottom: 0; width: 100%; height: 5px; background: var(--brand-gold); }

  .brand-tab { position: absolute; left: 113px; top: 26px; width: 62px; height: 60px; background: var(--paper); }
  .brand-name {
    position: absolute;
    left: 23px; top: 98px;
    font-family: "Josefin Sans", sans-serif;
    font-weight: 600;
    font-size: 44px;
    letter-spacing: 3px;
    line-height: 1;
    color: var(--brand-gold);
  }

  .watermark-block {
    position: absolute;
    left: 655px; top: 60px;
    width: 360px; height: 388px;
    background: var(--gold-faint);
  }

  .contact {
    position: absolute;
    left: 24px; top: 378px;
    list-style: none;
    font-family: "Roboto Slab", serif;
    font-size: 15px;
    line-height: 1.2;
    color: var(--ink);
  }
  .contact li { display: flex; align-items: center; gap: 13px; height: 34px; white-space: nowrap; }
  .contact svg { width: 17px; height: 17px; flex: none; }
</style>
</head>
<body>

  <div class="envelope envelope--back-red">
    <svg class="flap" viewBox="0 0 1015 190" aria-hidden="true">
      <path d="M0 0 H1015 L1000 45 Q985 88 920 98 L575 172 Q507 186 440 172 L95 98 Q30 88 15 45 Z" fill="var(--brand-red)"/>
    </svg>
    <div class="flap-name">VARNOKO</div>
  </div>

  <div class="envelope envelope--back-black">
    <svg class="flap" viewBox="0 0 1015 190" aria-hidden="true">
      <path d="M0 0 H1015 L1000 45 Q985 88 920 98 L575 172 Q507 186 440 172 L95 98 Q30 88 15 45 Z" fill="var(--brand-black)"/>
    </svg>
    <div class="flap-name">VARNOKO</div>
  </div>

  <div class="envelope envelope--front">
    <div class="watermark-block"></div>
    <div class="front-band"></div>
    <div class="front-rule"></div>
    <div class="brand-tab"></div>
    <div class="brand-name">VARNOKO</div>

    <ul class="contact">
      <li>
        <svg viewBox="0 0 24 24" aria-hidden="true"><path d="M12 2a7 7 0 0 0-7 7c0 5 7 13 7 13s7-8 7-13a7 7 0 0 0-7-7zm0 9.5A2.5 2.5 0 1 1 12 6.5a2.5 2.5 0 0 1 0 5z" fill="var(--brand-red)"/></svg>
        Street Name, City Name State Zipcode
      </li>
      <li>
        <svg viewBox="0 0 24 24" aria-hidden="true" fill="none" stroke="var(--brand-red)" stroke-width="1.6"><circle cx="12" cy="12" r="9"/><ellipse cx="12" cy="12" rx="4" ry="9"/><path d="M3 12h18M5 7h14M5 17h14"/></svg>
        www.varnoko.com
      </li>
    </ul>
    <div class="front-base"></div>
  </div>

</body>
</html>
```